Website Design for a different kind of Business Consulting organisation needed!

We need a website design that reflects who we are, the simplicity of our consulting business and with a focus on our priority - to help our clients deliver, or execute - the "e" in Vantor-i.

Our key high level requirements are:
1) Simple and intuitive look and feel
2) Integration with all key social media platforms, twitter, facebook, linkedin, tumblr.

10 pages, tops.
- Main page - Welcome
- About Us/ Who are Vantor-i?
- 5 services pages - Project Management, Business Process Management, Change Management, Business Analysis and Finance Systems
- Contact Us

Something like:
http://www.lumvexhold.example/

Vantor-i is a registered trademark and all Logos and other branded material are attached for reference.

So, what’s our gig: A few snippets from previous work...

We are a different kind of business consulting group. We partner with our clients to help them deliver change. We don't just provide them with the theory. We also provide them with the leadership and capability to execute the change.

We aren’t a one stop shop, and we don’t offer cookie cutter solutions. We’re a boutique consulting firm covering Project Management, Business Process Management, Change Management and Business Analytics.

Vantor-i is a professional services organisation that partners with their clients to lead the execution of strategic process and system improvement initiatives. Vantor-i combines hands on delivery with coaching in best practice methodologies and approaches to build their clients capabilities to ensure their ongoing success in project implementations.

UPDATES:

Thanks to everyone who has submitted designs so far. The standard of designs coming through is quite high, with lots of professional designs that nail the design brief. Eliminating them is proving to be quite challenging.

A few updates to the job brief:
- Please make sure the design fits on one page. We would like all of our information to be on the first page that people see without them having to scroll down
- Please ensure you include the FIVE services we offer in the design
- Please use corporate images/istock photos in your designs which are relevant to our business
- Please add a section for a live twitter feed from our twitter account and a link to google+
- Please add a section for news/updates

Also, if you are able to build a site once a design is selected, please let us know.

Thanks,

Maribel.

Target Market(s)

Our target customers are large enterprises in Australia that are growing rapidly and have recently (last 24 months) undertaken or are currently undergoing software implementations and business process improvement programs. These businesses have a turnover of $100m or above and are working hard to differentiate themselves from their competitors but are not seeing the return on investment promised by software vendors and process improvement initiatives.

Industry/Entity Type

Leadership

Requirements
Must have
• Collaboration / Training / Workshop / Consulting images all of a professional nature.
Simple, non-cluttered look with plenty of white space.

```html
<!DOCTYPE html>
<html lang="en">
<head>
<meta charset="utf-8">
<title>Vantor-i | Business Consulting</title>
<link href="https://fonts.googleapis.com/css2?family=Open+Sans:wght@300;400;600;700&display=swap" rel="stylesheet">
<style>
  :root {
    --brand-blue: #0a4f9f;
    --text-dark: #3d3d3d;
    --text-body: #444444;
    --icon-grey: #b4b4b4;
    --hero-light: #eceeef;
    --white: #ffffff;
  }
  * { margin: 0; padding: 0; box-sizing: border-box; }
  html, body { width: 1176px; height: 1200px; overflow: hidden; }
  body {
    position: relative;
    background: var(--white);
    font-family: "Open Sans", Arial, sans-serif;
    color: var(--text-body);
  }
  .top-rule { position: absolute; left: 0; top: 0; width: 1176px; height: 6px; background: var(--brand-blue); }

  .site-header { position: absolute; left: 0; top: 6px; width: 1176px; height: 106px; }
  .brand { position: absolute; left: 116px; top: 20px; display: flex; align-items: center; gap: 10px; }
  .brand-name { font-size: 46px; font-weight: 400; color: var(--brand-blue); letter-spacing: 1px; line-height: 1; }
  .brand-dot { width: 14px; height: 14px; border-radius: 50%; background: var(--brand-blue); }

  .social-top { position: absolute; left: 943px; top: 12px; display: flex; gap: 11px; }
  .social-top span { width: 31px; height: 31px; border-radius: 50%; background: var(--icon-grey); }
  .social-top span.is-active { background: var(--brand-blue); }

  .main-nav { position: absolute; left: 528px; top: 66px; display: flex; gap: 34px; font-size: 14.5px; font-weight: 600; color: #5a5a5a; }
  .main-nav .is-current { color: var(--brand-blue); }

  .hero { position: absolute; left: 0; top: 112px; width: 1176px; height: 459px; overflow: hidden; }
  .hero-photo {
    position: absolute; inset: 0;
    background: linear-gradient(90deg, #6d6e6a 0%, #8f8a80 18%, #5e5a55 35%, #a7a7a3 52%, #dcdedf 62%, var(--hero-light) 80%, #f2f3f3 100%);
  }
  .hero-copy { position: absolute; left: 588px; top: 80px; width: 480px; text-align: center; }
  .hero-title { font-size: 40px; font-weight: 700; color: #2e2e2e; letter-spacing: 0.5px; }
  .hero-text { margin-top: 14px; font-size: 17.5px; font-weight: 300; line-height: 26px; color: #2e2e2e; }
  .hero-button {
    display: inline-block; margin-top: 33px; width: 144px; height: 47px; line-height: 47px;
    background: var(--brand-blue); color: var(--white); font-size: 15px; font-weight: 400;
  }
  .slider-dots { position: absolute; left: 568px; top: 426px; display: flex; gap: 9px; }
  .slider-dots span { width: 11px; height: 11px; border-radius: 50%; background: #d8d8d8; }
  .slider-dots span.is-active { background: var(--brand-blue); }

  .welcome { position: absolute; left: 0; top: 612px; width: 1176px; text-align: center; }
  .welcome-title { font-size: 29px; font-weight: 400; color: var(--text-dark); }
  .welcome-text { width: 960px; margin: 8px auto 0; font-size: 16px; line-height: 29px; color: var(--text-body); }

  .services { position: absolute; left: 0; top: 766px; width: 1176px; }
  .service { position: absolute; width: 176px; }
  .service-icon { width: 98px; height: 98px; border-radius: 50%; background: var(--icon-grey); margin: 0 auto; }
  .service.is-active .service-icon { background: var(--brand-blue); }
  .service-title { margin-top: 22px; height: 44px; text-align: center; font-size: 17px; font-weight: 600; line-height: 21px; color: var(--text-dark); }
  .service.is-active .service-title { color: var(--brand-blue); }
  .service-text { margin-top: 17px; font-size: 14px; line-height: 22.5px; color: var(--text-body); }

  .site-footer { position: absolute; left: 0; top: 1077px; width: 1176px; height: 123px; background: var(--brand-blue); color: var(--white); }
  .footer-col { position: absolute; top: 20px; font-size: 12px; line-height: 19px; }
  .footer-heading { font-size: 13.5px; font-weight: 700; line-height: 18px; margin-bottom: 1px; }
  .social-footer { display: flex; gap: 10px; margin-top: 8px; }
  .social-footer span { width: 32px; height: 32px; border-radius: 50%; background: var(--white); }
  .footer-links { display: flex; gap: 30px; }
  .footer-brand { position: absolute; left: 848px; top: 22px; }
  .footer-brand-name { display: flex; align-items: center; gap: 8px; font-size: 36px; font-weight: 400; line-height: 1; letter-spacing: 1px; }
  .footer-brand-name i { width: 11px; height: 11px; border-radius: 50%; background: var(--white); display: block; }
  .copyright { margin-top: 12px; font-size: 12px; }
</style>
</head>
<body>
  <div class="top-rule"></div>

  <header class="site-header">
    <div class="brand">
      <span class="brand-name">Vantor-i</span>
      <span class="brand-dot"></span>
    </div>
    <div class="social-top" aria-label="Social links">
      <span aria-label="Social network one"></span>
      <span aria-label="Social network two"></span>
      <span class="is-active" aria-label="Social network three"></span>
    </div>
    <nav class="main-nav">
      <span class="is-current">HOME</span>
      <span>ABOUT</span>
      <span>SERVICES</span>
      <span>PORTFOLIO</span>
      <span>BLOG</span>
      <span>CONTACT</span>
    </nav>
  </header>

  <section class="hero">
    <div class="hero-photo" role="img" aria-label="Photo of a consultant writing on a clipboard in a warehouse aisle, blending into a bright open office"></div>
    <div class="hero-copy">
      <h1 class="hero-title">Lorem Ipsum Dolor</h1>
      <p class="hero-text">We are professional services organisation that partners with their clients to lead the execution of strategic process and system improvement initiatives</p>
      <span class="hero-button">Find out more</span>
    </div>
    <div class="slider-dots">
      <span></span><span class="is-active"></span><span></span><span></span>
    </div>
  </section>

  <section class="welcome">
    <h2 class="welcome-title">Welcome to Vantor-i</h2>
    <p class="welcome-text">We partner with our clients to help them deliver change. We don't just provide them with the theory. We also provide them with the leadership and capability to execute the change.</p>
  </section>

  <section class="services">
    <div class="service" style="left:115px">
      <div class="service-icon" role="img" aria-label="Organisation chart pictogram"></div>
      <h3 class="service-title">Project<br>Management</h3>
      <p class="service-text">Sed ut perspiciatis unde omnis iste natus error sit it dolorem que.</p>
    </div>
    <div class="service" style="left:307px">
      <div class="service-icon" role="img" aria-label="Presenter and team pictogram"></div>
      <h3 class="service-title">Business Process<br>Management</h3>
      <p class="service-text">Tempor dolor sit amet it sicing elit sed do eiusm it does tempor.</p>
    </div>
    <div class="service is-active" style="left:499px">
      <div class="service-icon" role="img" aria-label="Two people exchanging pictogram"></div>
      <h3 class="service-title">Change<br>Management</h3>
      <p class="service-text">Lorem ipsum dolor sit erit amet consectetur adipisip eiusmod sed mentor.</p>
    </div>
    <div class="service" style="left:693px">
      <div class="service-icon" role="img" aria-label="Person with chart pictogram"></div>
      <h3 class="service-title">Business<br>Analysis</h3>
      <p class="service-text">Dolor orem ipsum mando my sitem amet consectret ur adipisicing elit sed do.</p>
    </div>
    <div class="service" style="left:887px">
      <div class="service-icon" role="img" aria-label="Person with gears pictogram"></div>
      <h3 class="service-title">Business<br>Intelligence</h3>
      <p class="service-text">Dolor orem ipsum mando my sitem amet consectret ur adipisicing elit sed do.</p>
    </div>
  </section>

  <footer class="site-footer">
    <div class="footer-col" style="left:118px">
      <div class="footer-heading">CONNECT WITH US</div>
      <div>on social media network</div>
      <div class="social-footer">
        <span aria-label="Social network one"></span>
        <span aria-label="Social network two"></span>
        <span aria-label="Social network three"></span>
      </div>
    </div>
    <div class="footer-col" style="left:324px">
      <div class="footer-heading">PAGES</div>
      <div class="footer-links">
        <div>Home<br>About<br>Services</div>
        <div>Term &amp; Conditions<br>FAQ<br>Porfolio</div>
      </div>
    </div>
    <div class="footer-col" style="left:557px">
      <div class="footer-heading">CONTACT DETAILS</div>
      <div>p: +61 3 400 118 205&nbsp; f: +61 3 9000 4412<br>Level 4, 18 Harlow Lane, Melbourne,<br>Australia, 3000</div>
    </div>
    <div class="footer-brand">
      <div class="footer-brand-name">Vantor-i<i></i></div>
      <div class="copyright">Copyright © 2014 All Rights Reserved</div>
    </div>
  </footer>
</body>
</html>
```